Brellwick Partners, LLC Stationary

Brellwick Partners, LLC is a new financial planning and consulting company. We are looking for designs on business cards, letterhead, envelopes, and anything else that would be useful. Our preference for business card design is two sided. We are looking for a professional and clean look with incorporating the logo and patriotic feel. Thank you to all who participate and good luck!

```html
<!DOCTYPE html>
<html lang="en">
<head>
<meta charset="utf-8">
<title>Brellwick Partners, LLC — Business Card</title>
<link rel="stylesheet" href="https://fonts.googleapis.com/css2?family=Roboto:wght@300;400;500;700&display=swap">
<style>
  :root {
    --navy: #123c6b;
    --navy-deep: #0e335d;
    --red: #c8202f;
    --white: #ffffff;
    --ink-soft: #6d7582;
    --backdrop: #ecebe8;
  }
  * { margin: 0; padding: 0; box-sizing: border-box; }
  html, body { width: 1200px; height: 950px; overflow: hidden; }
  body {
    background: var(--backdrop);
    font-family: "Roboto", Arial, sans-serif;
    position: relative;
  }
  .card {
    position: absolute;
    left: 220px;
    width: 760px;
    height: 434px;
    border-radius: 4px;
    overflow: hidden;
    box-shadow: 0 6px 18px rgba(0,0,0,.18);
  }
  .card--front { top: 30px; background: var(--white); }
  .card--back { top: 490px; background: var(--navy); }
  .card__shape { position: absolute; inset: 0; width: 100%; height: 100%; }

  .brand {
    position: absolute;
    left: 40px;
    top: 180px;
    display: flex;
    align-items: center;
    gap: 14px;
  }
  .brand__square { width: 26px; height: 26px; background: var(--red); flex: none; }
  .brand__name {
    color: var(--navy);
    font-weight: 500;
    font-size: 28px;
    letter-spacing: 1.5px;
    line-height: 1.08;
    text-transform: uppercase;
  }
  .brand__tagline {
    position: absolute;
    left: 80px;
    top: 252px;
    font-size: 9.5px;
    letter-spacing: 2px;
    color: var(--ink-soft);
    text-transform: uppercase;
    white-space: nowrap;
  }

  .contact {
    position: absolute;
    left: 505px;
    top: 44px;
    color: var(--white);
  }
  .contact__name { font-size: 22px; font-weight: 700; letter-spacing: 1px; text-transform: uppercase; }
  .contact__role { font-size: 17px; font-weight: 300; letter-spacing: 1px; text-transform: uppercase; margin-top: 4px; }
  .contact__address { font-size: 16px; font-weight: 300; line-height: 1.45; margin-top: 14px; }
  .contact__lines { list-style: none; margin-top: 22px; font-size: 16px; font-weight: 300; line-height: 1.6; }
  .contact__lines li { display: flex; align-items: center; justify-content: space-between; width: 222px; }
  .contact__icon { width: 15px; height: 15px; fill: var(--white); }

  .back__brand {
    position: absolute;
    inset: 0;
    display: flex;
    flex-direction: column;
    align-items: center;
    justify-content: center;
    gap: 18px;
    color: var(--white);
  }
  .back__name { font-size: 40px; font-weight: 500; letter-spacing: 3px; text-transform: uppercase; display: flex; align-items: center; gap: 18px; }
  .back__square { width: 30px; height: 30px; background: var(--red); }
  .back__web { font-size: 17px; font-weight: 300; letter-spacing: 2px; }
</style>
</head>
<body>

<section class="card card--front" aria-label="Business card front">
  <svg class="card__shape" viewBox="0 0 760 434" preserveAspectRatio="none" aria-hidden="true">
    <path d="M440 0 C 510 140, 370 250, 290 360 C 260 400, 230 425, 220 434 L 208 434 C 225 420, 250 395, 278 356 C 358 246, 495 138, 428 0 Z" fill="var(--red)"/>
    <path d="M452 0 C 520 140, 385 252, 305 362 C 275 402, 245 426, 236 434 L 760 434 L 760 0 Z" fill="var(--navy)"/>
  </svg>

  <div class="brand">
    <span class="brand__square"></span>
    <span class="brand__name">Brellwick<br>Partners, LLC</span>
  </div>
  <p class="brand__tagline">Financial Planning and Consulting</p>

  <div class="contact">
    <p class="contact__name">Daniel Hartley</p>
    <p class="contact__role">CEO / Founder</p>
    <p class="contact__address">4120 Larchmont Way<br>Juneau, Alaska 99801</p>
    <ul class="contact__lines">
      <li>555 310 4821
        <svg class="contact__icon" viewBox="0 0 24 24" aria-hidden="true"><path d="M6.6 10.8a15.1 15.1 0 0 0 6.6 6.6l2.2-2.2a1 1 0 0 1 1-.25 11.4 11.4 0 0 0 3.6.57 1 1 0 0 1 1 1V20a1 1 0 0 1-1 1A17 17 0 0 1 3 4a1 1 0 0 1 1-1h3.5a1 1 0 0 1 1 1c0 1.25.2 2.45.57 3.57a1 1 0 0 1-.25 1z"/></svg>
      </li>
      <li>555 310 4822
        <svg class="contact__icon" viewBox="0 0 24 24" aria-hidden="true"><rect x="2" y="6" width="20" height="12" rx="1"/><rect x="5" y="9" width="14" height="2" fill="var(--navy)"/></svg>
      </li>
      <li>hello@brellwick.com
        <svg class="contact__icon" viewBox="0 0 24 24" aria-hidden="true"><path d="M2 5h20v14H2z M3 6l9 7 9-7" fill="none" stroke="var(--white)" stroke-width="2"/></svg>
      </li>
      <li>www.brellwick.com
        <svg class="contact__icon" viewBox="0 0 24 24" aria-hidden="true"><circle cx="12" cy="12" r="9" fill="none" stroke="var(--white)" stroke-width="2"/><path d="M3 12h18M12 3c3 3 3 15 0 18M12 3c-3 3-3 15 0 18" fill="none" stroke="var(--white)" stroke-width="1.6"/></svg>
      </li>
    </ul>
  </div>
</section>

<section class="card card--back" aria-label="Business card back">
  <div class="back__brand">
    <p class="back__name"><span class="back__square"></span>Brellwick Partners, LLC</p>
    <p class="back__web">www.brellwick.com</p>
  </div>
</section>

</body>
</html>
```